Need a small Brochure Designing for a High Tech LED Spotlight

This is an expensive product and the best of it's kind in the world, so it needs to be marketed to intelligent, forward thinking people who appreciate and pay for excellent design and innovation. The type of people who buy Quince products i guess. It needs to be clean. The colours do not need to be in keep with our website, but our logo does need to be on the brochure. I have attached a dcoument with all the text, the order the text goes in and an idea of how i want the first page to look. All images and logos have been attached too.

Target Market(s)

This is aimed at people with high disposible incomes who spend money on the best designed products and the latest technology. The type of people who buy Quince products.

Industry/Entity Type

Product

Requirements
Must have
• The work needs to be editable by us using indesign

The pages need to be A5. I'm not sure how many pages the brochure needs to be as it does need to be clean and be spaced out well. On the file that contains the text i've indicated that 8 pages would be good.

The logos i attached - 1) Brava Product Design Award, 2) K Technology Award, 3) Tall Oak Design Award and 4) Keen Form Award all need to be at the bottom of the front page, quite small, but still able to see them well.

- Needs to have a QR code so that smart phones can scan the code and be taken to a zen pier clip - QR code is attached.
- Needs to have Tumbolt Icon - @BrightNookCo
Nice to have
• Nice to remind customers on each page that the product has a 5 year Warranty and we have a 365 day Returns Policy.

```html
<!DOCTYPE html>
<html lang="en">
<head>
<meta charset="utf-8">
<title>Pellar 7 LED Spotlight Brochure – Introduction Spread</title>
<link href="https://fonts.googleapis.com/css2?family=Questrial&display=swap" rel="stylesheet">
<style>
  :root {
    --canvas: #ffffff;
    --page: #ffffff;
    --ink: #2b2b2b;
    --ink-soft: #3a3a3a;
    --brand-green: #3a8f3a;
    --quote-mark: #e3ebe1;
    --panel: rgba(255, 255, 255, 0.84);
    --photo-light: #f6eee2;
    --photo-mid: #e6d7c3;
    --photo-warm: #c99a6a;
  }
  * { box-sizing: border-box; margin: 0; padding: 0; }
  html, body {
    width: 1200px; height: 900px; overflow: hidden;
    background: var(--canvas);
    font-family: "Questrial", "Century Gothic", sans-serif;
    color: var(--ink);
  }
  .spread {
    position: absolute; left: 75px; top: 88px;
    width: 1125px; height: 708px;
    overflow: hidden;
    box-shadow: 0 1px 4px rgba(0,0,0,0.12);
  }
  .hero-photo {
    position: absolute; left: 0; top: 0; width: 1005px; height: 708px;
    background:
      radial-gradient(ellipse at 22% 15%, #fff8ec 0%, transparent 40%),
      linear-gradient(180deg, var(--photo-light) 0%, #efe5d6 45%, var(--photo-mid) 75%, var(--photo-warm) 100%);
  }
  .right-page {
    position: absolute; left: 1005px; top: 0; width: 120px; height: 708px;
    background: var(--page); overflow: hidden;
  }
  .quote-mark {
    position: absolute; left: 0; top: 0; width: 120px; height: 200px;
    fill: var(--quote-mark);
  }
  .text-panel {
    position: absolute; left: 28px; top: 322px; width: 977px; height: 342px;
    background: var(--panel);
  }
  .section-title {
    color: var(--brand-green); font-size: 19px; font-weight: 700;
    letter-spacing: 0.1px;
  }
  .intro-title { position: absolute; left: 33px; top: 20px; }
  .column {
    position: absolute; width: 431px;
    font-size: 14.2px; line-height: 17.2px; color: var(--ink-soft);
    text-align: justify;
  }
  .column p { margin-bottom: 17px; }
  .column-left { left: 33px; top: 59px; }
  .column-right { left: 487px; top: 59px; }
  .lead { font-weight: 700; color: var(--ink); }
  .quote { font-style: italic; }
  .heat-title { position: absolute; left: 61px; top: 342px; white-space: nowrap; }
  .heat-copy {
    position: absolute; left: 61px; top: 381px; width: 300px;
    font-size: 14.2px; line-height: 16.8px; color: var(--ink-soft);
    white-space: nowrap;
  }
  .heat-copy p { margin-bottom: 16px; }
</style>
</head>
<body>
  <div class="spread">
    <div class="hero-photo" role="img" aria-label="Bright white modern kitchen with black pendant lamps, recessed LED spotlights, white cabinetry and a timber floor"></div>

    <div class="text-panel">
      <h2 class="section-title intro-title">Introduction</h2>
      <div class="column column-left">
        <p class="lead">With its unrivalled performance and quality, the Pellar 7 7w is the most technologically advanced LED Spotlight in the word.</p>
        <p><span class="quote">“LEDs used to be prohibitively expensive, but advances in semiconductor technology mean they’re now brighter and more affordable than before… it’s easy to see why they’re becoming so popular.”</span> Verdict?</p>
        <p>BrightNook Managing Director Dana Whitlow talks about the Pellar 7 7w LED Spot:</p>
        <p class="quote">“I’ve been working with the manufacturer of this exceptional product since their inception in 2008. They’ve received more than a hundred world patents and safety certifications so far – as far as I am concerned, there isn’t an LED manufacturer in the</p>
      </div>
      <div class="column column-right">
        <p class="quote">world that comes close to their expertise and attention to detail.</p>
        <p class="quote">“Since its creation, the company has won a number of prestigious international design awards, such as the Brava Product Design Award, the K Technology Award, the Tall Oak Design Award, and the Keen Form Award.</p>
        <p class="quote">“With high-quality, industry-leading performance, they’ve become the first choice for professional buyers and lighting designers in recent years. They’re basically the Quince of the LED lighting industry – we’re talking beautifully designed products that are miles ahead of the competition”</p>
        <p class="quote">“The Pellar 7 Is The Ultimate In Lighting For The Discerning, Design Conscious And Forward Thinking Person”</p>
      </div>
    </div>

    <div class="right-page">
      <svg class="quote-mark" viewBox="0 0 120 200" aria-hidden="true">
        <path d="M44 0 C26 45 10 110 4 196 L120 198 L120 92 L78 92 C82 55 96 22 114 0 Z"/>
      </svg>
      <h2 class="section-title heat-title">Heat Dissipation</h2>
      <div class="heat-copy">
        <p>The brightness of any LED,<br>though, is limited by its<br>heat.</p>
        <p>Heat is the enemy of LEDs,<br>the critical factor in lifespan.<br>So if the spotlight has poor<br>heat dissipation, it fails at<br>unacceptable rates.</p>
        <p>The Pellar 7 7w uses cutting<br>edge heat sinks inspired by<br>AstroLab space engineering.</p>
        <p>This beautiful design has won<br>awards.</p>
      </div>
    </div>
  </div>
</body>
</html>
```